Flyer-Design zum Animieren von Buchkäufen
Zielgruppe
Buchkäufer
Aufgabenstellung
Der Flyer soll zum Buchkauf animieren. Ausgelegt/verteilt wird er in Buchhandlungen, Museen, Ausstellungen.
Es handelt sich um ein geschichtswissenschaftliches Buch, der Flyer sollte diesen Charakter darstellen.

```html
<!DOCTYPE html>
<html lang="de">
<head>
<meta charset="utf-8">
<title>Flyer – Markgrafen! Hier endet der Weg</title>
<link rel="stylesheet" href="https://fonts.googleapis.com/css2?family=Jost:wght@400;500&family=Big+Shoulders+Display:wght@200&display=swap">
<style>
  :root {
    --bg: #e6e6e6;
    --flyer-dark: #1c1b1a;
    --flyer-mid: #3a3632;
    --white: #f5f3ef;
    --cover-dark: #232220;
  }
  * { margin: 0; padding: 0; box-sizing: border-box; }
  html, body { width: 1200px; height: 900px; overflow: hidden; background: var(--bg); }
  .canvas { position: relative; width: 1200px; height: 900px; }

  .flyer {
    position: absolute; left: 400px; top: 25px; width: 400px; height: 850px;
    background: var(--flyer-dark); overflow: hidden;
    box-shadow: 0 10px 30px rgba(0,0,0,.25);
  }
  .flyer__backdrop {
    position: absolute; inset: 0;
    background:
      radial-gradient(ellipse 55% 22% at 35% 52%, rgba(201,138,62,.75), transparent 70%),
      radial-gradient(ellipse 70% 25% at 40% 30%, rgba(120,125,130,.55), transparent 70%),
      radial-gradient(ellipse 60% 20% at 30% 78%, rgba(120,85,45,.6), transparent 70%),
      linear-gradient(180deg, #2a2826 0%, var(--flyer-mid) 40%, #2b241d 75%, var(--flyer-dark) 100%);
  }
  .flyer__headline {
    position: absolute; top: 70px; left: 0; width: 100%; text-align: center;
    font-family: "Jost", sans-serif; font-weight: 400; color: var(--white);
    font-size: 52px; line-height: 1.0; letter-spacing: .5px;
  }
  .flyer__subline {
    position: absolute; top: 195px; left: 0; width: 100%; text-align: center;
    font-family: "Jost", sans-serif; font-size: 12.5px; line-height: 1.45; color: var(--white);
  }

  .cover {
    position: absolute; left: 62px; top: 270px; width: 310px; height: 450px;
    background: var(--cover-dark); overflow: hidden;
    box-shadow: 0 6px 18px rgba(0,0,0,.5);
  }
  .cover__art {
    position: absolute; left: 0; right: 0; top: 130px; bottom: 0;
    background:
      radial-gradient(ellipse 30% 18% at 42% 28%, rgba(240,150,60,.85), transparent 70%),
      radial-gradient(ellipse 35% 40% at 72% 45%, rgba(225,222,215,.55), transparent 70%),
      linear-gradient(180deg, #5a4a42 0%, #6e4e42 35%, #45403b 65%, #2a2826 100%);
  }
  .cover__title {
    position: absolute; top: 22px; right: 16px; width: 280px; text-align: right;
    font-family: "Jost", sans-serif; font-weight: 500; color: var(--white); line-height: 1.05;
  }
  .cover__title-main { display: block; font-size: 30px; }
  .cover__title-line { display: block; font-size: 24px; }
  .cover__affair { display: block; margin-top: 6px; font-size: 12.5px; letter-spacing: .5px; }
  .cover__year { display: block; font-size: 14px; }

  .flyer__series {
    position: absolute; top: 738px; left: 0; width: 100%; text-align: center;
    font-family: "Big Shoulders Display", sans-serif; font-weight: 200;
    font-size: 30px; color: var(--white); letter-spacing: .5px;
  }
  .flyer__author {
    position: absolute; top: 786px; left: 0; width: 100%; text-align: center;
    font-family: "Jost", sans-serif; font-weight: 500; font-size: 19px; color: var(--white);
    letter-spacing: 1px;
  }
</style>
</head>
<body>
<main class="canvas">
  <article class="flyer">
    <div class="flyer__backdrop" role="img" aria-label="Unscharfes Hintergrundfoto in Dunkelgrau und Bernstein"></div>

    <h1 class="flyer__headline">Mehr<br>als ein Buch</h1>
    <p class="flyer__subline">die Auswirkungen der Brunnsteiner Affäre<br>nach einer wahren Begebenheit</p>

    <section class="cover">
      <div class="cover__art" role="img" aria-label="Buchcover-Illustration: Fachwerkhaus, Soldat im 18.-Jahrhundert-Gewand mit Muskete, Kampfszene im Torbogen"></div>
      <h2 class="cover__title">
        <span class="cover__title-main">Markgrafen!</span>
        <span class="cover__title-line">Hier endet der Weg</span>
        <span class="cover__affair">Die Brunnsteiner Affäre</span>
        <span class="cover__year">1792</span>
      </h2>
    </section>

    <p class="flyer__series">COLLECTANEA BRUNNSTEINENSIA 1770/1819</p>
    <p class="flyer__author">AUTOR NAME</p>
  </article>
</main>
</body>
</html>
```